Banner ad design for Vorlix Display Ads

We are looking for a designer to develop a concept for banner ads for a Vorlix Display campaign we are building.

We have 3 business lines, shredding services, records management services and scanning services.

We are looking for 4 sets of ads to be created, one for each business line + one set that showcases all of our lines together.

For the design concepts, we would like to see a few sizes (banner, square, leaderboard, skyscraper, etc) for each.

The person chosen will then need to create the ads into all Vorlix supported sizes -- 20 sizes total for each set of ads as per the Vorlix size guidelines found on this page - https://help.vorlix.com/vorlix-ads/answer/5830417?hl=en&ref_topic=6402871#

A few items to note:
- Design should complement our existing brand/website look and feel (www.tamrock-dunes.ca)
- Each final ad must be 150Kb or less in size
- Final designs should be editable, meaning if we would like to change some copy in the design, we can do so using a well-known software (Canva, Photoshop/InDesign, etc)
- Some images are attached for use, but if you feel a different stock image is more suitable to to your design, please go ahead and use it.

Provided below is some messaging that can be used for each set of ads. Do not feel you need to use all of the messaging, it is provided for guidance.

SHREDDING SERVICES:

Possible Short Headline:
-- One-Time Shredding Services
-- Secure Shredding Services
-- Affordable On-Site Shredding

Possible Long Headline
-- Your Paper Can be Destroyed as Soon as the Next Business Day

Possible Descriptions:
-- TORV QQQ Certified On site shredding company. Service as soon as Next Day.
-- Secure and Affordable Toronto & GTA On-Site Shredding.
-- Certified, Affordable Office Shredding Since 2003.
-- Quick, no contact and affordable paper shredding services in Toronto & Southern Ontario.
-- Certified, Affordable Office Shredding Since 2003. Fast, no contact shredding service.

Call to Action
-- Get a Quote

RECORDS MANAGEMENT
Short Headline:
-- Off-site Records Storage
-- Records Management & Storage
-- Secure Records Storage
-- Records Management Services
-- Long Term Records Management
-- Document Storage Solutions

Possible Description
-- Local, Affordable Storage Solutions. Protect and Store your Documents in our Secure Facility
-- Local, Affordable Records Management Solutions. Store your Records in our Secure Facility
-- Certified, Affordable Document Storage Since 2004. Contact Us for a Free Quote!
-- Veltra+ Certified, Affordable Document Storage Since 2004. Contact Us for a Free Quote!

Call to Action
-- Get a Quote

SCANNING SERVICES

Short Headline:
-- Professional Scanning Company
-- Toronto & GTA Scanning Service
-- Document Scanning Services
-- Digital Conversion Services
-- Fast & Easy Retrieval

Description
-- Scan and documents and files with Professional scanning services from Tamrock-Dunes
-- Convert Your Paper Files to Electronic Files. Fast & Easy Retrieval.
-- Easily access your documents electronically with Document Scanning Services

Call to Action
-- Get a Quote

ALL SERVICES AD SET
Short Headline
-- Shred, Scan & Store Documents
-- Secure Shredding, Records Management and Scanning Services
-- #1 Document Management Company
-- Tamrock Dunes Shredding, Storage & Scanning

Description
-- Secure and Affordable Toronto & GTA On-Site Shredding, Document Storage & Scanning Company

Call to Action
-- Get a Quote

Font styles to use
Sans Serif

```html
<!DOCTYPE html>
<html lang="en">
<head>
<meta charset="utf-8">
<title>Tamrock-Dunes – One-Time Shredding Services</title>
<link rel="stylesheet" href="https://fonts.googleapis.com/css2?family=Arimo:wght@400;700&display=swap">
<style>
  :root {
    --white: #ffffff;
    --name-navy: #0d3a68;
    --tagline-grey: #333333;
    --band-top: #2b8ad0;
    --band-bottom: #1566ad;
    --sub-navy: #0f3765;
    --cta-green: #20c25a;
    --photo-light: #d9d4c8;
    --photo-mid: #b9b2a2;
  }
  html, body {
    margin: 0;
    padding: 0;
    width: 1200px;
    height: 2400px;
    overflow: hidden;
    background: var(--white);
  }
  .ad {
    position: relative;
    width: 1200px;
    height: 2400px;
    font-family: "Arimo", Arial, sans-serif;
    overflow: hidden;
  }
  .brand {
    position: absolute;
    left: 0;
    top: 0;
    width: 1200px;
    height: 548px;
    background: var(--white);
    display: flex;
    flex-direction: column;
    align-items: center;
    justify-content: center;
  }
  .brand-row {
    display: flex;
    align-items: center;
    gap: 32px;
  }
  .brand-dot {
    width: 64px;
    height: 64px;
    border-radius: 50%;
    background: var(--name-navy);
  }
  .brand-name {
    margin: 0;
    font-size: 100px;
    font-weight: 700;
    color: var(--name-navy);
    line-height: 1;
  }
  .brand-tagline {
    margin: 40px 0 0;
    font-size: 64px;
    font-weight: 400;
    color: var(--tagline-grey);
    line-height: 1;
  }
  .hero-photo {
    position: absolute;
    left: 0;
    top: 548px;
    width: 1200px;
    height: 672px;
    background:
      linear-gradient(90deg, rgba(216,184,74,0.35) 0%, rgba(216,184,74,0.15) 45%, rgba(255,255,255,0) 70%),
      linear-gradient(180deg, var(--photo-light) 0%, var(--photo-mid) 70%, #8f8a80 100%);
  }
  .offer {
    position: absolute;
    left: 0;
    top: 1220px;
    width: 1200px;
    height: 1180px;
    background: linear-gradient(180deg, var(--band-top) 0%, var(--band-bottom) 100%);
    text-align: center;
  }
  .offer-headline {
    position: absolute;
    left: 0;
    top: 100px;
    width: 1200px;
    margin: 0;
    font-size: 150px;
    font-weight: 700;
    line-height: 180px;
    color: var(--white);
  }
  .offer-sub {
    position: absolute;
    left: 140px;
    top: 650px;
    width: 920px;
    margin: 0;
    font-size: 76px;
    font-weight: 400;
    line-height: 100px;
    color: var(--sub-navy);
  }
  .cta {
    position: absolute;
    left: 280px;
    top: 950px;
    width: 660px;
    height: 136px;
    background: var(--cta-green);
    color: var(--white);
    font-size: 72px;
    font-weight: 400;
    line-height: 136px;
    text-align: center;
    text-decoration: none;
  }
</style>
</head>
<body>
  <main class="ad">
    <header class="brand">
      <div class="brand-row">
        <span class="brand-dot" aria-hidden="true"></span>
        <p class="brand-name">Tamrock-Dunes</p>
      </div>
      <p class="brand-tagline">Information Security</p>
    </header>

    <div class="hero-photo" role="img" aria-label="Office worker at a desk surrounded by stacks of paper files and yellow and grey archive boxes"></div>

    <section class="offer">
      <h1 class="offer-headline">ONE-TIME<br>SHREDDING<br>SERVICES</h1>
      <p class="offer-sub">Your Paper Can be<br>Destroyed as Soon as<br>the Next Business Day</p>
      <a class="cta" href="#">Get a Quote</a>
    </section>
  </main>
</body>
</html>
```